Landing Page / Waitlist

I would like a landing page for people to sign up for a waiting list. The text on the page should include (but is not limited to):
1) Main point: The accounting system you'll love
2) Secondary points:
a. Ruthlessly efficient
b. Quietly intelligent
c. Driven by AI
I've attached a file of our logo

The design should be simple, clean, and innovative - this is an ai company

```html
<!DOCTYPE html>
<html lang="en">
<head>
<meta charset="utf-8">
<title>Tallyra — The Accounting System You'll Love</title>
<link href="https://fonts.googleapis.com/css2?family=Poppins:ital,wght@0,300;0,400;0,500;0,600;0,700;1,300;1,400&display=swap" rel="stylesheet">
<style>
:root{
  --hero-deep:#0a3f9e;
  --hero-mid:#0d5bc4;
  --sky:#0aa3f5;
  --bright:#0b8ff7;
  --azure:#1a8cf0;
  --ink:#0b0b12;
  --body-grey:#6d6f78;
  --white:#ffffff;
  --footer:#0e3a93;
  --footer-deep:#0a2f80;
}
*{margin:0;padding:0;box-sizing:border-box}
html,body{width:1200px;height:2377px;overflow:hidden}
body{font-family:'Poppins',sans-serif;color:var(--ink);background:var(--white);position:relative}
.abs{position:absolute}
.btn{position:absolute;display:flex;align-items:center;justify-content:center;gap:22px;border-radius:26px;background:linear-gradient(90deg,#0ab0f8,#0a8cf2);color:var(--white);font-weight:600;text-transform:uppercase;letter-spacing:-.2px}
.btn svg{width:14px;height:14px}

/* hero */
.hero{position:absolute;left:0;top:0;width:1200px;height:612px;background:radial-gradient(ellipse at 70% 55%,#1470d6 0%,var(--hero-mid) 35%,var(--hero-deep) 100%)}
.brand{position:absolute;display:flex;align-items:center;gap:10px;font-weight:500}
.brand .dot{width:20px;height:20px;border-radius:50%}
.hero .brand{left:143px;top:56px;font-size:26px;color:#c9d3e8}
.hero .brand .dot{background:var(--sky)}
.menu{position:absolute;left:1018px;top:38px;width:40px}
.menu span{display:block;height:3px;background:var(--white);border-radius:2px;margin-bottom:8px;margin-left:auto}
.hero h1{position:absolute;left:143px;top:174px;font-size:46px;line-height:58px;font-weight:700;color:var(--white)}
.hero h1 .accent{color:var(--sky);display:block;padding-left:46px;position:relative}
.hero h1 .accent::before{content:"";position:absolute;left:2px;top:20px;width:24px;height:24px;border-radius:50%;background:var(--sky)}
.hero h1 .light{font-weight:500}
.hero .tag{position:absolute;left:144px;top:303px;font-size:19px;font-weight:500;color:var(--white)}
.hero .lede{position:absolute;left:144px;top:343px;width:420px;font-size:14.5px;line-height:24px;color:var(--white)}
.hero .btn{left:142px;top:427px;width:232px;height:48px;font-size:15px}
.hero-art{position:absolute;left:540px;top:90px;width:560px;height:490px;border-radius:30px;background:radial-gradient(ellipse at 70% 45%,rgba(220,235,255,.55) 0%,rgba(40,140,240,.45) 40%,rgba(10,70,170,0) 75%)}

/* about */
.about{position:absolute;left:0;top:612px;width:1200px;height:585px;background:linear-gradient(180deg,#fff 70%,#eef3fc 100%)}
.about-art{position:absolute;left:145px;top:58px;width:365px;height:460px;background:linear-gradient(150deg,#0ab0f8,#0a7ef0);border-radius:6px}
.section-title{font-size:37px;font-weight:700;line-height:46px}
.section-title .soft{font-weight:400}
.about .section-title{position:absolute;left:624px;top:104px}
.about .section-title .soft{color:var(--azure)}
.about .lead{position:absolute;left:624px;top:162px;width:432px;font-size:17.5px;line-height:29px}
.about .copy{position:absolute;left:624px;top:226px;width:432px;font-size:14px;line-height:24px;color:var(--body-grey);text-align:justify;font-weight:300}
.about .btn{left:625px;top:403px;width:152px;height:44px;font-size:14.5px;gap:14px}

/* value */
.value{position:absolute;left:0;top:1197px;width:1200px;height:551px}
.value-panel{position:absolute;left:0;top:0;width:600px;height:551px;background:linear-gradient(180deg,#0a9af8,#0b8ef5)}
.value-art{position:absolute;left:600px;top:0;width:600px;height:551px;background:radial-gradient(ellipse at 55% 45%,#1e72e0 0%,#0f48b5 55%,#0b2f8c 100%)}
.value .section-title{position:absolute;left:145px;top:46px;color:var(--white)}
.pillar{position:absolute;left:143px;width:450px;height:118px}
.hex{position:absolute;left:0;top:0;width:103px;height:118px}
.pillar h3{position:absolute;left:131px;top:20px;font-size:18px;font-weight:500;color:var(--white)}
.pillar p{position:absolute;left:131px;top:52px;width:300px;font-size:14px;line-height:23px;color:var(--white)}

/* testimonials */
.voices{position:absolute;left:0;top:1748px;width:1200px;height:407px;text-align:center}
.voices .section-title{position:absolute;left:0;top:70px;width:1200px}
.quote-mark{position:absolute;left:575px;top:144px}
.voices blockquote{position:absolute;left:210px;top:200px;width:780px;font-size:14.5px;line-height:23px;font-style:italic;font-weight:300;color:#5a5c66}
.voices .name{position:absolute;left:0;top:288px;width:1200px;font-size:18px}
.voices .role{position:absolute;left:0;top:316px;width:1200px;font-size:11.5px;color:var(--azure)}
.arrow{position:absolute;top:218px;width:40px;height:40px;border-radius:50%;display:flex;align-items:center;justify-content:center}
.arrow.prev{left:88px;border:1px solid #d5d8e0;background:#fff}
.arrow.next{left:1072px;background:var(--azure)}

/* footer */
.footer{position:absolute;left:0;top:2155px;width:1200px;height:222px;background:radial-gradient(ellipse at 50% 60%,#154aa6 0%,var(--footer) 50%,var(--footer-deep) 100%)}
.footer .brand{left:143px;top:70px;font-size:28px;color:var(--white)}
.footer .brand .dot{background:var(--white)}
.footer .note{position:absolute;left:640px;top:48px;width:420px;font-size:14px;line-height:24px;color:var(--white)}
.footer .btn{left:640px;top:110px;width:200px;height:44px;font-size:14px;gap:16px}
.footer .rule{position:absolute;left:143px;top:175px;width:914px;height:1px;background:rgba(255,255,255,.6)}
.footer .copy{position:absolute;left:0;top:187px;width:1200px;text-align:center;font-size:14px;color:var(--white)}
</style>
</head>
<body>

<section class="hero">
  <div class="brand"><span class="dot"></span>Tallyra</div>
  <div class="menu"><span style="width:36px"></span><span style="width:40px"></span><span style="width:28px"></span></div>
  <div class="hero-art" role="img" aria-label="Robot figure emerging from a smartphone, holding a glowing chip, with circuit light trails"></div>
  <h1><span class="accent">The Accounting</span>System <span class="light">You'll Love</span></h1>
  <p class="tag">Effortless. Intelligent. Future-Ready.</p>
  <p class="lede">Experience Accounting That Saves Time, Reduces Stress, and Thinks Ahead So You Don't Have To</p>
  <a class="btn">Join the Waitlist
    <svg viewBox="0 0 14 14" fill="none" stroke="#fff" stroke-width="2"><path d="M2 12L12 2M4 2h8v8"/></svg></a>
</section>

<section class="about">
  <div class="about-art" role="img" aria-label="Large brand emblem filled with circuit-board imagery"></div>
  <h2 class="section-title"><span class="soft">About</span> Tallyra</h2>
  <p class="lead">Lorem ipsum dolor sit amet consectetur adipiscing elit, sed do eiusmod tempor incididunt</p>
  <p class="copy">Sed ut perspiciatis unde omnis iste natus error sit voluptatem accusantium doloremque laudantium, totam rem aperiam, eaque ipsa quae ab illo inventore veritatis et quasi architecto beatae vitae dicta sunt explicabo. Nemo enim ipsam voluptatem quia voluptas sit aspernatur aut odit aut fugit, sed quia consequuntur magni dolores eos qui ratione</p>
  <a class="btn">Read More
    <svg viewBox="0 0 14 14" fill="none" stroke="#fff" stroke-width="2"><path d="M2 12L12 2M4 2h8v8"/></svg></a>
</section>

<section class="value">
  <div class="value-panel"></div>
  <div class="value-art" role="img" aria-label="Digital human head in profile with a glowing hand holding a floating emblem"></div>
  <h2 class="section-title"><span class="soft">Value</span> Proposition</h2>

  <div class="pillar" style="top:118px">
    <svg class="hex" viewBox="0 0 103 118"><polygon points="51.5,2 101,30 101,88 51.5,116 2,88 2,30" fill="#fff" stroke="#0a8ef5" stroke-width="3"/><polygon points="51.5,8 96,33 96,85 51.5,110 7,85 7,33" fill="none" stroke="#0a8ef5" stroke-width="1.5"/><circle cx="51.5" cy="59" r="16" fill="none" stroke="#0a8ef5" stroke-width="6"/></svg>
    <h3>Ruthlessly Efficient</h3>
    <p>Automate busywork, streamline workflows, and close books faster than ever.</p>
  </div>
  <div class="pillar" style="top:246px">
    <svg class="hex" viewBox="0 0 103 118"><polygon points="51.5,2 101,30 101,88 51.5,116 2,88 2,30" fill="#fff" stroke="#0a8ef5" stroke-width="3"/><polygon points="51.5,8 96,33 96,85 51.5,110 7,85 7,33" fill="none" stroke="#0a8ef5" stroke-width="1.5"/><circle cx="51.5" cy="59" r="16" fill="none" stroke="#0a8ef5" stroke-width="6"/></svg>
    <h3>Quietly Intelligent</h3>
    <p>Smart suggestions, anomaly detection,and predictive insights available only when you need them.</p>
  </div>
  <div class="pillar" style="top:374px">
    <svg class="hex" viewBox="0 0 103 118"><polygon points="51.5,2 101,30 101,88 51.5,116 2,88 2,30" fill="#fff" stroke="#0a8ef5" stroke-width="3"/><polygon points="51.5,8 96,33 96,85 51.5,110 7,85 7,33" fill="none" stroke="#0a8ef5" stroke-width="1.5"/><circle cx="51.5" cy="59" r="16" fill="none" stroke="#0a8ef5" stroke-width="6"/></svg>
    <h3>AI-Driven</h3>
    <p>Built from the ground up using modern AI not just patched-on automation like legacy systems.</p>
  </div>
</section>

<section class="voices">
  <h2 class="section-title">What Our <span class="soft">Clients</span> Say</h2>
  <svg class="quote-mark" width="50" height="36" viewBox="0 0 50 36" fill="none" stroke="#1a8cf0" stroke-width="2.5"><path d="M2 2h20v14l-8 18H6l6-14H2z"/><path d="M28 2h20v14l-8 18h-8l6-14h-10z"/></svg>
  <blockquote>Lorem ipsum dolor sit amet, consectetur adipiscing elit, sed do eiustmod tempor incididunt ut laboreet dolore magna aliqua Ut enim ad minim veniam, quis nostrud exercitation ullamco laboris nisi ut aliquip ex ea commodo consequat aute irure dolor in reprehenderit</blockquote>
  <p class="name">Mara Ellis</p>
  <p class="role">Lorem ipsum dolor</p>
  <span class="arrow prev"><svg width="18" height="12" viewBox="0 0 18 12" fill="none" stroke="#111" stroke-width="1.6"><path d="M17 6H2M7 1L2 6l5 5"/></svg></span>
  <span class="arrow next"><svg width="18" height="12" viewBox="0 0 18 12" fill="none" stroke="#fff" stroke-width="1.6"><path d="M1 6h15M11 1l5 5-5 5"/></svg></span>
</section>

<footer class="footer">
  <div class="brand"><span class="dot"></span>Tallyra</div>
  <p class="note">Sed ut perspiciatis unde omnis iste natus error sit voluptatem accusantium doloremque laudantium,</p>
  <a class="btn">Join the Waitlist
    <svg viewBox="0 0 14 14" fill="none" stroke="#fff" stroke-width="2"><path d="M2 12L12 2M4 2h8v8"/></svg></a>
  <div class="rule"></div>
  <p class="copy">© 2025 Tallyra - All Rights Reserved</p>
</footer>

</body>
</html>
```